Business Card - high end, modern health care

Hey designers!

We need a double sided business card for the boutique, cutting edge physical therapy rehabilitation centre in Sydney's Northern Beaches.

With the most qualified physios in the area The Harbourview Motion Clinic does what other physiotherapy practices do not, we take our time with our patients giving them longer appointments, better physios and therefor faster results!

We guarantee that the service people receive at THMC will be unparalleled.

Hence we need a business card to reflect our modern, boutique, high end service. The final design needs to reflect that we are in a class of our own yet with the feel of beachside retreat.

Below I have attached our logo in both blue on white and white on blue. The exact colour is;
and the font that we have used in our logo is Tex Gyre Aventador.

I like the idea of the blue as the main colour as it is more eye catching and our signage onto the main road will be in this blue and in the interest of consistency across marketing the blue needs to be a part of the design. However I would appreciate a few designs onto a wooden background as this is a visual theme within the fitout of the practice.

The design needs to be of standard size (91x55mm).

Target Market(s)

We target people who have an end outcome in mind and those who have had poor experiences with other providers and ensure that everyone gets the care that they deserve with a premium service that is tailored to the individuals circumstances. As a premium service, the target market is highly educated, business and tech savvy with the additional target market of elderly people who have self funded their retirement and see value in paying for the best ongoing rehabilitation to maintain independence.

Industry/Entity Type

Physical Therapy

Contact Information for Business Card

Name, designation( Titled Musculoskeletal Physiotherapist... there will also be those in the company that have multiple designations ie 5 or 6 words long), phone number, email, facebook, instagram, address

Font styles to use
Sans Serif

Colors

Designer to choose colors to be used in the design.

Requirements
Must have
• Front - The logo as large as possible, blue or wooden theme, and all of the important details.
• Back - A blank space/lines on which to write appointment times (no "Appointment, date, time" etc.)
Nice to have
• facebook url
• logos for facebook and instagram
• Mini logos for the phone and email?

```html
<!DOCTYPE html>
<html lang="en">
<head>
<meta charset="utf-8">
<title>The Harbourview Motion Clinic – Business Card</title>
<link rel="stylesheet" href="https://fonts.googleapis.com/css2?family=Raleway:wght@400;500;700&display=swap">
<style>
  :root {
    --stage: #5a5a7c;
    --brand-blue: #0f58a8;
    --paper: #ffffff;
    --ink: #1a1a1a;
    --rule: #2b2b2b;
    --dash: #b9b9b9;
    --social-a: #1e88d0;
    --social-b: #e8508a;
  }
  * { margin: 0; padding: 0; box-sizing: border-box; }
  html, body { width: 1200px; height: 1000px; overflow: hidden; }
  body {
    position: relative;
    background: var(--stage);
    font-family: "Raleway", sans-serif;
    color: var(--ink);
  }
  .card { position: absolute; width: 658px; height: 375px; }

  /* Front */
  .card-front {
    left: 136px; top: 78px;
    background: var(--brand-blue);
    display: flex; flex-direction: column; align-items: center;
  }
  .front-mark {
    margin-top: 70px;
    width: 184px; height: 184px;
    border-radius: 50%;
    background: var(--paper);
  }
  .front-name {
    margin-top: 22px;
    color: var(--paper);
    font-weight: 700;
    font-size: 20px;
    line-height: 1.15;
    letter-spacing: 0.04em;
    text-align: center;
    text-transform: uppercase;
  }

  /* Back */
  .card-back {
    left: 437px; top: 548px;
    background: var(--paper);
  }
  .person { position: absolute; left: 41px; top: 80px; }
  .person-name { font-size: 25px; font-weight: 400; line-height: 1; }
  .person-name .accent { color: var(--brand-blue); }
  .person-title { margin-top: 12px; font-size: 15px; }

  .rule { position: absolute; left: 41px; width: 577px; height: 0; border-top: 1.3px solid var(--rule); }
  .rule-top { top: 147px; }
  .rule-bottom { top: 242px; }

  .contact { position: absolute; display: flex; align-items: center; gap: 15px; font-size: 18px; }
  .contact svg { width: 24px; height: 24px; }
  .contact-phone { left: 42px; top: 169px; }
  .contact-mail { left: 42px; top: 200px; }

  .social { position: absolute; display: flex; align-items: center; gap: 9px; font-size: 15.5px; color: #333; }
  .social .dot { width: 21px; height: 21px; border-radius: 50%; }
  .social-profile { left: 410px; top: 170px; }
  .social-profile .dot { background: var(--social-a); }
  .social-gallery { left: 410px; top: 201px; }
  .social-gallery .dot { background: var(--social-b); }

  .back-brand {
    position: absolute; left: 0; right: 0; top: 256px;
    display: flex; justify-content: center; align-items: center; gap: 8px;
    color: var(--brand-blue);
  }
  .back-brand .dot { width: 34px; height: 34px; border-radius: 50%; background: var(--brand-blue); }
  .back-brand-name { font-weight: 700; font-size: 15px; line-height: 1.1; letter-spacing: 0.03em; text-transform: uppercase; }

  .write-line {
    position: absolute; left: 41px; top: 338px; width: 577px; height: 0;
    border-top: 1.5px dashed var(--dash);
  }
</style>
</head>
<body>
  <section class="card card-front">
    <div class="front-mark"></div>
    <div class="front-name">The Harbourview<br>Motion Clinic</div>
  </section>

  <section class="card card-back">
    <div class="person">
      <p class="person-name">Name of <span class="accent">Person</span></p>
      <p class="person-title">Designation</p>
    </div>
    <div class="rule rule-top"></div>

    <div class="contact contact-phone">
      <svg viewBox="0 0 24 24" aria-hidden="true">
        <circle cx="12" cy="12" r="10.5" fill="none" stroke="#1a1a1a" stroke-width="1.6"/>
        <path d="M8.6 6.8c.5-.4 1.1-.3 1.4.2l1 1.7c.3.5.1 1-.3 1.3l-.6.4c.5 1.3 1.5 2.4 2.8 3l.5-.6c.3-.4.9-.5 1.3-.2l1.6 1.1c.5.3.6 1 .2 1.4l-.8.9c-.7.7-3 .4-5.3-1.9S7 8.2 7.7 7.5z" fill="#1a1a1a"/>
      </svg>
      <span>555.010.2376</span>
    </div>
    <div class="contact contact-mail">
      <svg viewBox="0 0 24 24" aria-hidden="true">
        <rect x="1.5" y="5" width="21" height="14" fill="#1a1a1a"/>
        <path d="M1.5 5l10.5 8 10.5-8M1.5 19l8-7M22.5 19l-8-7" fill="none" stroke="#fff" stroke-width="1.3"/>
      </svg>
      <span>hello@harbourviewmotion.com</span>
    </div>

    <div class="social social-profile"><span class="dot"></span><span>profile/name</span></div>
    <div class="social social-gallery"><span class="dot"></span><span>gallery_name</span></div>

    <div class="rule rule-bottom"></div>

    <div class="back-brand">
      <span class="dot"></span>
      <span class="back-brand-name">The Harbourview<br>Motion Clinic</span>
    </div>

    <div class="write-line"></div>
  </section>
</body>
</html>
```